Bright Campus Network Sign

We need a sign that can be displayed on the front fence of schools that shows that will proudly proclaim that the school is an BCN School
The Bright Campus Network is one of the world's leading organisations suppprting schools to become innovative and adaptive organisations.
Updates

The signs are being cut from 2400x1200 boards Signs are 55x40 can be either orientation

Target Market(s)

Parents and educators

Industry/Entity Type

Education

Requirements
Must have
• Edgy. Professional. NOT conservative. Crisp.
• Colours and styles to match existing logos
Nice to have
• The Marlowe Advisory logo is just for reference as it is the parent company. ONLY want reference to BCN.
• Keep it simple. Not too busy. Elegant but edgy
Should not have
• No symbols to do with traditioanl education. NO PENS, MORTAR BOARDS, BOOKS

```html
<!DOCTYPE html>
<html lang="en">
<head>
<meta charset="utf-8">
<title>Bright Campus Network Sign</title>
<link href="https://fonts.googleapis.com/css2?family=Cinzel:wght@500;600&display=swap" rel="stylesheet">
<style>
  :root {
    --purple: #522c7f;
    --green: #5b7d33;
    --paper: #ffffff;
    --purple-soft: rgba(82, 44, 127, 0.22);
    --green-soft: rgba(91, 125, 51, 0.22);
  }
  * { margin: 0; padding: 0; box-sizing: border-box; }
  html, body {
    width: 1200px;
    height: 874px;
    overflow: hidden;
    background: var(--paper);
  }
  .sign {
    position: relative;
    width: 1200px;
    height: 874px;
    background: var(--paper);
    font-family: "Cinzel", "Trajan Pro", serif;
    overflow: hidden;
  }
  .brand {
    position: absolute;
    left: 100px;
    top: 70px;
    width: 390px;
    text-align: center;
    color: var(--purple);
    font-weight: 600;
  }
  .brand-dot {
    display: block;
    width: 70px;
    height: 70px;
    margin: 0 auto 14px;
    border-radius: 50%;
    background: var(--green);
  }
  .brand-initials {
    display: block;
    font-size: 104px;
    line-height: 1;
    letter-spacing: 2px;
  }
  .brand-name {
    display: block;
    margin-top: 16px;
    font-size: 27px;
    line-height: 1;
    letter-spacing: 0.5px;
  }
  .brand-rule {
    display: block;
    height: 2px;
    margin-top: 12px;
    background: var(--green);
  }
  .headline {
    position: absolute;
    left: 100px;
    top: 566px;
    font-weight: 600;
    font-size: 78px;
    line-height: 98px;
    letter-spacing: 1px;
  }
  .headline span { display: block; }
  .headline .green { color: var(--green); }
  .headline .purple { color: var(--purple); }
  .tree-art {
    position: absolute;
    left: 640px;
    top: 0;
    width: 560px;
    height: 830px;
    border-radius: 50% 0 0 40% / 45% 0 0 30%;
    background:
      radial-gradient(ellipse at 35% 35%, var(--purple-soft), transparent 60%),
      radial-gradient(ellipse at 70% 55%, var(--green-soft), transparent 60%),
      linear-gradient(160deg, rgba(82, 44, 127, 0.12), rgba(91, 125, 51, 0.12));
  }
</style>
</head>
<body>
  <main class="sign">
    <div class="brand">
      <span class="brand-dot"></span>
      <span class="brand-initials">BCN</span>
      <span class="brand-name">BRIGHT CAMPUS NETWORK</span>
      <span class="brand-rule"></span>
    </div>

    <h1 class="headline">
      <span class="green">Transforming</span>
      <span class="green">Schools</span>
      <span class="purple">Together</span>
    </h1>

    <div class="tree-art" role="img" aria-label="Large decorative tree of purple and green leaves rising from two stylised figures"></div>
  </main>
</body>
</html>
```